design a construction company business card

Design business card around our logo. Card must have all the typical info: name, title, address, phone, email, business name, etc. Somewhere on the card I would like to see our motto "Built on integrity... Inspired by commitment." Consider adding a splash of bright orange to the card to complement the blues and silvers/grays in the logo. We are open to metallic inks, textures, etc. We would like to see options on both light and dark backgrounds. The font in the logo is Euro Technic Extended Regular.

```html
<!DOCTYPE html>
<html lang="en">
<head>
<meta charset="utf-8">
<title>Harlow Contracting business card</title>
<link rel="stylesheet" href="https://fonts.googleapis.com/css2?family=Michroma&family=Orbitron:wght@700&display=swap">
<style>
  :root {
    --backdrop: #2b2b2c;
    --card: #1f1f20;
    --ink-white: #f2f2f2;
    --ink-silver: #b9bcc0;
    --ink-blue: #2f7fd0;
    --divider: #d8d8d8;
  }
  * { margin: 0; padding: 0; box-sizing: border-box; }
  html, body {
    width: 1200px;
    height: 901px;
    overflow: hidden;
    background: var(--backdrop);
    font-family: "Michroma", sans-serif;
  }
  .sheet {
    width: 1200px;
    height: 901px;
    display: flex;
    flex-direction: column;
    align-items: center;
    justify-content: center;
    gap: 44px;
  }
  .card {
    position: relative;
    width: 680px;
    height: 388px;
    background: var(--card);
    box-shadow: 0 10px 30px rgba(0,0,0,0.45);
  }

  /* Front face */
  .card-front {
    display: flex;
    flex-direction: column;
    align-items: center;
    justify-content: center;
  }
  .brand {
    display: flex;
    align-items: center;
    gap: 14px;
    color: var(--ink-silver);
    font-size: 30px;
    letter-spacing: 2px;
    margin-top: -20px;
  }
  .brand-mark {
    width: 22px;
    height: 22px;
    background: var(--ink-silver);
  }
  .brand-sub {
    margin-top: 10px;
    color: var(--ink-silver);
    font-size: 11px;
    letter-spacing: 3px;
  }
  .motto {
    position: absolute;
    bottom: 56px;
    left: 0;
    right: 0;
    text-align: center;
    color: var(--ink-blue);
    font-size: 12px;
    letter-spacing: 1.5px;
  }

  /* Back face */
  .identity {
    position: absolute;
    top: 150px;
    right: 368px;
    text-align: right;
  }
  .person-name {
    font-family: "Orbitron", sans-serif;
    font-weight: 700;
    color: var(--ink-white);
    font-size: 25px;
    letter-spacing: 1px;
  }
  .person-title {
    margin-top: 6px;
    color: var(--ink-blue);
    font-size: 15px;
  }
  .divider {
    position: absolute;
    top: 150px;
    left: 332px;
    width: 2px;
    height: 62px;
    background: var(--divider);
  }
  .contact-list {
    position: absolute;
    top: 150px;
    left: 352px;
    list-style: none;
    color: var(--ink-white);
    font-size: 13px;
  }
  .contact-list li {
    display: flex;
    align-items: center;
    gap: 12px;
    height: 21px;
  }
  .contact-list svg { width: 12px; height: 12px; flex: none; }
  .web-name { color: var(--ink-blue); }
  .address {
    position: absolute;
    bottom: 64px;
    left: 150px;
    display: flex;
    align-items: center;
    gap: 8px;
    color: var(--ink-white);
    font-size: 13px;
  }
  .address svg { width: 11px; height: 15px; }
</style>
</head>
<body>
<main class="sheet">
  <section class="card card-front" aria-label="Card front">
    <div class="brand"><span class="brand-mark"></span>HARLOW</div>
    <div class="brand-sub">CONTRACTING, INC.</div>
    <p class="motto">"Built on integrity... Inspired by commitment."</p>
  </section>

  <section class="card card-back" aria-label="Card back">
    <div class="identity">
      <h1 class="person-name">DANA WHITFORD</h1>
      <p class="person-title">Ceo &amp; Founder</p>
    </div>
    <div class="divider"></div>
    <ul class="contact-list">
      <li>
        <svg viewBox="0 0 12 12" aria-hidden="true"><path d="M3 1 L5 3.5 L4 4.8 Q5 7 7.2 8 L8.5 7 L11 9 L10 11 Q4 11 1 2 Z" fill="var(--ink-blue)"/></svg>
        000 111 2223
      </li>
      <li>
        <svg viewBox="0 0 12 12" aria-hidden="true"><rect x="1" y="2.5" width="10" height="7" fill="none" stroke="var(--ink-blue)" stroke-width="1.2"/><path d="M1 2.5 L6 6.5 L11 2.5" fill="none" stroke="var(--ink-blue)" stroke-width="1.2"/></svg>
        urname@email.com
      </li>
      <li>
        <svg viewBox="0 0 12 12" aria-hidden="true"><circle cx="6" cy="6" r="5" fill="none" stroke="var(--ink-blue)" stroke-width="1.2"/><ellipse cx="6" cy="6" rx="2" ry="5" fill="none" stroke="var(--ink-blue)" stroke-width="1"/><path d="M1 6 H11" stroke="var(--ink-blue)" stroke-width="1"/></svg>
        <span>www.<span class="web-name">ursitename</span>.com</span>
      </li>
    </ul>
    <p class="address">
      <svg viewBox="0 0 11 15" aria-hidden="true"><path d="M5.5 0 A5.5 5.5 0 0 1 11 5.5 C11 9 5.5 15 5.5 15 C5.5 15 0 9 0 5.5 A5.5 5.5 0 0 1 5.5 0 Z" fill="var(--ink-blue)"/><circle cx="5.5" cy="5.5" r="2" fill="var(--card)"/></svg>
      Your Street Address, UnitedStates, 1234
    </p>
  </section>
</main>
</body>
</html>
```